The design should look similar to the uploaded example to accommodate the information needed for a business card template. I would like to see the colors orange and charcoal grey incorporated along with the logo.The following should be on the back of the card SPECIALIZING IN NEW AND USED TIRES & WHEELS FOR:- Loaders- Skid Steers- Telehandlers- Boom Lifts- Forklifs and moreELIMINATING DOWNTIMEWheel Exchange Program for New & Used Foam Filled and Solid Rubber TiresSPECIALTY SERVICES- Foam Filling Tires- Largest Tire Press in SE- ONSITE Forklift Tire Press- Boom Truck Services - Rubber Tracks

Target Market(s)

New and Existing Customers

Industry/Entity Type

Business

Contact Information for Business Card

NAMEHEAVY DUTY TIRE, LLC8470 Belvedere RoadWest Palm Beach, FL 33411P: 844-HD-TIRESF: 561-431-6469C:E: W: WWW.GRANITERIMSUPPLY-EXAMPLE.COM

Font styles to use
Sans Serif

Colors
f37122
333333

Requirements
Must have
• The logo and the information indicated for the backside of the card
Nice to have
• Keep the orange and charcoal grey colors

```html
<!DOCTYPE html>
<html lang="en">
<head>
<meta charset="utf-8">
<title>Granite Rim Supply – Business Card</title>
<link rel="stylesheet" href="https://fonts.googleapis.com/css2?family=Source+Sans+3:wght@400;600;700&display=swap">
<style>
  :root {
    --orange: #f58a42;
    --charcoal: #333333;
    --white: #ffffff;
    --backdrop: #e9e7e4;
  }
  * { box-sizing: border-box; margin: 0; padding: 0; }
  html, body { width: 1200px; height: 900px; overflow: hidden; }
  body {
    background: var(--backdrop);
    font-family: "Source Sans 3", "Myriad Pro", Arial, sans-serif;
    color: var(--white);
    position: relative;
  }
  .card {
    position: absolute;
    background: var(--orange);
    overflow: hidden;
    box-shadow: 0 4px 14px rgba(0,0,0,0.18);
  }
  .card-front { left: 237px; top: 60px; width: 556px; height: 345px; }
  .card-back  { left: 457px; top: 518px; width: 560px; height: 344px; }

  .brand-mark {
    position: absolute;
    left: -8px; top: 8px;
    width: 330px; height: 330px;
    border-radius: 50%;
    background: var(--charcoal);
    display: flex; align-items: center; justify-content: center;
  }
  .brand-name {
    font-weight: 700;
    font-size: 44px;
    line-height: 1.05;
    text-align: center;
    color: var(--white);
    letter-spacing: 1px;
  }

  .contact {
    position: absolute;
    right: 23px; top: 46px;
    text-align: right;
  }
  .contact-name { font-size: 21px; font-weight: 600; line-height: 28px; }
  .contact-company { font-size: 14.5px; margin-top: 8px; line-height: 20px; }
  .contact-lines { list-style: none; margin-top: 14px; }
  .contact-lines li {
    font-size: 14.5px; line-height: 23.3px;
    display: flex; justify-content: flex-end; align-items: center; gap: 7px;
  }
  .contact-lines svg { width: 11px; height: 11px; fill: var(--white); }
  .contact-address { font-size: 14.5px; line-height: 23px; margin-top: 19px; }

  .back-content {
    position: absolute; inset: 0;
    text-align: center;
    padding-top: 35px;
    font-weight: 600;
  }
  .back-title { font-size: 17px; font-weight: 700; line-height: 22px; }
  .equip-list { font-size: 15px; line-height: 23px; margin-top: 12px; }
  .bullet { display: inline-block; width: 6px; height: 6px; border-radius: 50%; background: var(--white); margin: 0 9px 2px 5px; vertical-align: middle; }
  .downtime { font-size: 15px; line-height: 20px; margin-top: 26px; }
  .services-title { font-size: 19.5px; font-weight: 700; margin-top: 25px; line-height: 24px; }
  .services-list { font-size: 15px; line-height: 23px; margin-top: 12px; }
</style>
</head>
<body>

<section class="card card-front" aria-label="Business card front">
  <div class="brand-mark">
    <div class="brand-name">GRANITE<br>RIM</div>
  </div>
  <div class="contact">
    <div class="contact-name">Marcus Delaney</div>
    <div class="contact-company">GRANITE RIM SUPPLY, LLC</div>
    <ul class="contact-lines">
      <li>844-GR-WHEEL
        <svg viewBox="0 0 12 12"><path d="M2.5 0.5l2 2.2-1 1.3c.7 1.6 1.9 2.8 3.5 3.5l1.3-1 2.2 2-1.2 2C5.8 10.3 1.7 6.2 0.5 1.7z"/></svg></li>
      <li>561-278-9053
        <svg viewBox="0 0 12 12"><path d="M3 0h5v3H3zM1 4h10v6H1zM3 6h2v1H3zm4 0h2v1H7zM3 8h2v1H3zm4 0h2v1H7z"/></svg></li>
      <li>123-456-7890
        <svg viewBox="0 0 12 12"><path d="M3 0h6v12H3zM4 1.5v8h4v-8zM5.5 10.2h1v1h-1z" fill-rule="evenodd"/></svg></li>
      <li>info@graniterim-example.com
        <svg viewBox="0 0 12 12"><path d="M0 2h12v8H0zM1 3l5 4 5-4z" fill-rule="evenodd"/></svg></li>
      <li>www.graniterimsupply-example.com
        <svg viewBox="0 0 12 12"><circle cx="6" cy="6" r="6"/></svg></li>
    </ul>
    <div class="contact-address">5126 Marston Lane<br>West Palm Beach, FL 33411</div>
  </div>
</section>

<section class="card card-back" aria-label="Business card back">
  <div class="back-content">
    <div class="back-title">SPECIALIZING IN NEW AND USED TIRES &amp; WHEELS FOR</div>
    <div class="equip-list">
      Loaders<span class="bullet"></span> Skid Steers <span class="bullet"></span> Telehandlers<span class="bullet"></span> Boom Lifts<br>
      Forklifs and more
    </div>
    <div class="downtime">
      ELIMINATING DOWNTIME<br>
      Wheel Exchange Program for New &amp; Used Foam<br>
      Filled and Solid Rubber Tires
    </div>
    <div class="services-title">SPECIALTY SERVICES</div>
    <div class="services-list">
      Foam Filling Tires<span class="bullet"></span> Largest Tire Press in SE<br>
      ONSITE Forklift Tire Press<span class="bullet"></span> Boom Truck Services<span class="bullet"></span> Rubber Tracks
    </div>
  </div>
</section>

</body>
</html>
```